Post it Note design

POST-IT NOTE DESIGN (CONTENT)
Size recommended: 4x6 for handwriting space.
Header (Bold):
Lighting Issue Detected on Your Property
Sub-header:
During our routine night inspection, we noted the following item(s):
Checkbox List:
⬜ Building Lights Out
⬜ Pole Lights Out
⬜ Sign Not Illuminated
⬜ Other ________________________
Action Line:
We can provide a quote or dispatch service right away.
Area for notes
Contact Block (Bold & Centered):
Quellmere Fixture Inc.
Service@QuellmereFixture.com
www.QuellmereFixture.com
877-514-6028
Industry/Entity Type
Electrical lighting
Colors
Designer to choose colors to be used in the design.
Look and feel
Each slider illustrates characteristics of the customer's brand and the style your logo design should communicate.

```html
<!DOCTYPE html>
<html lang="en">
<head>
<meta charset="utf-8">
<title>Lighting Issue Notes – Quellmere Fixture Inc.</title>
<link rel="stylesheet" href="https://fonts.googleapis.com/css2?family=Bebas+Neue&family=Roboto+Condensed:ital,wght@0,400;0,500;0,700;1,500&display=swap">
<style>
  :root {
    --navy: #0c1a8c;
    --navy-soft: #2541b2;
    --red: #d0152b;
    --ink: #1e1e22;
    --paper: #ffffff;
    --rule: #d3d3d8;
    --dot: #d6d6dc;
    --backdrop-light: #4b4b4d;
    --backdrop-dark: #1c1c1d;
  }
  * { box-sizing: border-box; margin: 0; padding: 0; }
  html, body { width: 1200px; height: 960px; overflow: hidden; }
  body {
    background: radial-gradient(ellipse at 50% 48%, var(--backdrop-light) 0%, #323233 45%, var(--backdrop-dark) 100%);
    font-family: "Roboto Condensed", "Arial Narrow", sans-serif;
    color: var(--ink);
    position: relative;
  }
  .note {
    position: absolute;
    top: 102px;
    width: 491px;
    height: 736px;
    background: var(--paper);
    box-shadow: 0 18px 22px rgba(0,0,0,0.55);
    overflow: hidden;
  }
  .note--dotted { left: 82px; }
  .note--ruled { left: 613px; }

  .note__title {
    font-family: "Bebas Neue", "Oswald", sans-serif;
    font-weight: 400;
    color: var(--paper);
    position: absolute;
  }
  .note__footer {
    position: absolute;
    left: 0; right: 0; bottom: 0;
    background: var(--navy);
    border-bottom: 8px solid var(--red);
    color: var(--paper);
    text-align: center;
    font-size: 13px;
    line-height: 17px;
    display: flex;
    flex-direction: column;
    justify-content: center;
  }
  .note__footer strong { font-weight: 700; }
  .contact-line span + span::before { content: "|"; margin: 0 6px; }

  .intro {
    position: absolute;
    left: 28px;
    font-size: 24px;
    line-height: 25px;
    font-weight: 500;
  }
  .checklist { list-style: none; position: absolute; font-size: 17px; font-weight: 500; }
  .checklist li { display: flex; align-items: center; gap: 9px; height: 25px; white-space: nowrap; }
  .checklist li::before {
    content: "";
    width: 12px; height: 12px;
    border: 1.5px solid var(--ink);
    flex: none;
  }

  /* dotted note */
  .note--dotted .header-shape { position: absolute; left: 0; top: 0; }
  .note--dotted .note__title {
    left: 28px; top: 22px;
    font-size: 47px; line-height: 45px;
    text-shadow: 2px 2px 0 var(--red);
    letter-spacing: -0.5px;
  }
  .query-mark {
    position: absolute; left: 404px; top: 16px;
    font-family: "Bebas Neue", sans-serif;
    font-size: 108px; line-height: 1;
    color: var(--navy-soft);
  }
  .brand-name {
    font-family: "Roboto Condensed", sans-serif;
    font-weight: 700;
    position: absolute;
    white-space: nowrap;
  }
  .note--dotted .brand-name { right: 30px; top: 108px; font-size: 19px; line-height: 22px; color: var(--paper); }
  .note--dotted .intro { top: 199px; }
  .note--dotted .checklist {
    left: 28px; top: 261px; width: 400px;
    display: grid; grid-template-columns: 185px 1fr;
  }
  .action-pill {
    position: absolute; left: 27px; top: 324px;
    width: 437px; height: 25px;
    border: 2px solid var(--red); border-radius: 13px;
    text-align: center;
    font-style: italic; font-weight: 500; font-size: 16px; line-height: 21px;
  }
  .notes-label {
    position: absolute; left: 28px; top: 364px;
    color: var(--red); font-size: 17px; font-weight: 500;
  }
  .notes-dots {
    position: absolute; left: 28px; top: 388px;
    width: 440px; height: 280px;
    background-image: radial-gradient(circle, var(--dot) 1.3px, transparent 1.6px);
    background-size: 21.6px 21.6px;
    background-position: -7px -7px;
  }
  .note--dotted .note__footer { height: 51px; }

  /* ruled note */
  .note--ruled .header-band {
    position: absolute; left: 0; top: 0; width: 100%; height: 154px;
    background: var(--navy);
  }
  .note--ruled .note__title {
    left: 0; right: 0; top: 32px;
    text-align: center;
    font-size: 56px; line-height: 50px;
  }
  .accent { color: var(--red); }
  .note--ruled .intro { top: 181px; line-height: 24.5px; }
  .note--ruled .checklist { left: 30px; top: 304px; }
  .note--ruled .checklist li::before { border-color: var(--red); border-width: 2px; }
  .note--ruled .action-text {
    position: absolute; left: 30px; top: 467px;
    font-style: italic; font-weight: 500;
    font-size: 16px; line-height: 19px; letter-spacing: 1.6px;
  }
  .note--ruled .brand-name { left: 30px; top: 588px; font-size: 22px; line-height: 24px; color: var(--navy); }
  .writing-lines {
    position: absolute; left: 217px; top: 191px;
    width: 241px; height: 487px;
    background: repeating-linear-gradient(to bottom, var(--rule) 0 1.5px, transparent 1.5px 30.3px);
  }
  .note--ruled .note__footer { height: 61px; padding-bottom: 4px; }
</style>
</head>
<body>

<section class="note note--dotted" aria-label="Lighting issue note with dotted notes area">
  <svg class="header-shape" width="491" height="210" viewBox="0 0 491 210" aria-hidden="true">
    <path d="M0 0 H491 V140 Q300 138 0 154 Z" fill="var(--navy)"/>
    <path d="M250 166 Q400 138 491 140 V202 Q430 164 250 166 Z" fill="var(--red)"/>
  </svg>
  <div class="query-mark" aria-hidden="true">?</div>
  <h1 class="note__title">Lighting Issue Detected<br>On Your Property</h1>
  <div class="brand-name">Quellmere Fixture Inc.</div>

  <p class="intro">During our routine night inspection,<br>we noted the following item(s):</p>
  <ul class="checklist">
    <li>Building Lights Out</li>
    <li>Sign Not Illuminated</li>
    <li>Pole Lights Out</li>
    <li>Other</li>
  </ul>
  <p class="action-pill">We can provide a quote or dispatch service right away.</p>
  <p class="notes-label">Notes</p>
  <div class="notes-dots" aria-hidden="true"></div>

  <footer class="note__footer">
    <strong>Quellmere Fixture Inc.</strong>
    <div class="contact-line"><span>Service@QuellmereFixture.com</span><span>www.QuellmereFixture.com</span><span>877-514-6028</span></div>
  </footer>
</section>

<section class="note note--ruled" aria-label="Lighting issue note with ruled writing lines">
  <div class="header-band"></div>
  <h1 class="note__title">Lighting Issue <span class="accent">Detected</span><br><span class="accent">On Your</span> Property</h1>

  <p class="intro">During our routine<br>night inspection,<br>we noted the<br>following item(s):</p>
  <ul class="checklist">
    <li>Building Lights Out</li>
    <li>Pole Lights Out</li>
    <li>Sign Not Illuminated</li>
    <li>Other</li>
  </ul>
  <p class="action-text">We can provide a<br>quote or dispatch<br>service right away.</p>
  <div class="brand-name">Quellmere<br>Fixture Inc.</div>
  <div class="writing-lines" aria-hidden="true"></div>

  <footer class="note__footer">
    <strong>Quellmere Fixture Inc.</strong>
    <div class="contact-line"><span>Service@QuellmereFixture.com</span><span>www.QuellmereFixture.com</span><span>877-514-6028</span></div>
  </footer>
</section>

</body>
</html>
```